Vantiqo custom business card design

Need a authentic, innovative business card design for a new mobile app business. I am uploading a few screen images from our app for you to view. I would like app design theme to match business card design. I can also send logo images.

```html
<!DOCTYPE html>
<html lang="en">
<head>
<meta charset="utf-8">
<title>Vantiqo Business Card</title>
<link href="https://fonts.googleapis.com/css2?family=Lato:wght@400;700;900&display=swap" rel="stylesheet">
<style>
  :root {
    --purple: #6a0b9a;
    --purple-deep: #5a0685;
    --purple-soft: #7d2bae;
    --ink: #1d1d1d;
    --paper: #ffffff;
    --rule: #d9d9d9;
    --stage: #e6e6e8;
  }
  * { margin: 0; padding: 0; box-sizing: border-box; }
  html, body { width: 1200px; height: 782px; overflow: hidden; }
  body {
    background: var(--stage);
    font-family: "Lato", Arial, sans-serif;
    position: relative;
  }
  .card {
    position: absolute;
    top: 236px;
    width: 540px;
    height: 309px;
    box-shadow: 0 6px 18px rgba(0,0,0,0.18);
  }
  .card-front { left: 40px; background: var(--paper); }
  .card-back {
    left: 620px;
    background: var(--purple);
  }
  .back-pattern {
    position: absolute; inset: 0;
    background: linear-gradient(135deg, var(--purple-soft), var(--purple) 55%, var(--purple-deep));
  }
  .back-badge {
    position: absolute;
    right: 120px; bottom: 70px;
    width: 46px; height: 46px;
    border-radius: 50%;
    background: var(--paper);
  }
  .brand {
    position: absolute;
    left: 34px; top: 122px;
    display: flex; align-items: center; gap: 12px;
  }
  .brand-dot {
    width: 34px; height: 34px;
    border-radius: 50%;
    background: var(--purple);
  }
  .brand-name {
    font-weight: 900;
    font-size: 40px;
    color: var(--ink);
    letter-spacing: 0.5px;
  }
  .divider {
    position: absolute;
    left: 262px; top: 46px;
    width: 1px; height: 220px;
    background: var(--rule);
  }
  .contact {
    position: absolute;
    left: 290px; top: 62px;
    color: var(--ink);
    font-size: 15px;
    line-height: 1.35;
  }
  .contact-name {
    font-weight: 900;
    font-size: 18px;
    color: var(--purple);
    letter-spacing: 0.4px;
  }
  .contact-role { margin-bottom: 4px; }
  .contact-line { display: flex; align-items: center; gap: 6px; }
  .contact-line svg { width: 12px; height: 12px; fill: var(--purple); flex: none; }
  .contact-address { margin-top: 2px; }
</style>
</head>
<body>
  <section class="card card-front">
    <div class="brand">
      <span class="brand-dot"></span>
      <span class="brand-name">Vantiqo</span>
    </div>
    <div class="divider"></div>
    <div class="contact">
      <div class="contact-name">MARCUS ELLERY</div>
      <div class="contact-role">Managing Director</div>
      <div class="contact-line">
        <svg viewBox="0 0 12 12"><path d="M2 1h2.5l1 3-1.5 1a6 6 0 0 0 3 3l1-1.5 3 1V10a1 1 0 0 1-1 1A9 9 0 0 1 1 2a1 1 0 0 1 1-1z"/></svg>
        <span>044-987 654 321</span>
      </div>
      <div class="contact-line">
        <svg viewBox="0 0 12 12"><path d="M3.5 0h5a1 1 0 0 1 1 1v10a1 1 0 0 1-1 1h-5a1 1 0 0 1-1-1V1a1 1 0 0 1 1-1zm0 2v7h5V2zm2.5 8a.6.6 0 1 0 0 1.2A.6.6 0 0 0 6 10z"/></svg>
        <span>044-987 654 322</span>
      </div>
      <div class="contact-line">
        <svg viewBox="0 0 12 12"><path d="M0 2h12v8H0zm1 1v.3l5 3.2 5-3.2V3zm0 1.5V9h10V4.5L6 7.7z"/></svg>
        <span>hello@vantiqo.app</span>
      </div>
      <div class="contact-line">
        <svg viewBox="0 0 12 12"><circle cx="6" cy="6" r="5.5"/></svg>
        <span>www.vantiqo.app</span>
      </div>
      <div class="contact-address">48, Harbour Lane West<br>Northbridge, 560210.</div>
    </div>
  </section>

  <section class="card card-back">
    <div class="back-pattern" role="img" aria-label="Repeating brand symbol pattern in soft purple tones"></div>
    <span class="back-badge"></span>
  </section>
</body>
</html>
```